Multi-Line Insurance PPC Landing Page - Conversion optimized.

We have a PPC landing page used for the general population to get an insurance quote through an agent's site.

We'd like to improve the page for PPC traffic, make it more conversion friendly.

Site should be a single long page.

We will dynamically change the form and headlines on the page depending on what insurance "line" is being called. ie, Lift, Auto, Home, Business.

The enclosed AI file has all of the raw elements we need. We're looking to enhance the design and conversion ability.

Target Market(s)

General public needed insurance services.

Industry/Entity Type

Insurance Broker

Number of Pages Required

1 page

Font styles to use
Sans Serif

Requirements
Must have
• Form, agent picture, name, address.

```html
<!DOCTYPE html>
<html lang="en">
<head>
<meta charset="utf-8">
<title>Insurance Agent – Get a Quote</title>
<link href="https://fonts.googleapis.com/css2?family=Open+Sans:wght@400;600;700&display=swap" rel="stylesheet">
<style>
:root{
  --blue:#1f5fae;
  --blue-dark:#174a8b;
  --navy:#123a6e;
  --green:#3d8b1e;
  --green-dark:#2f6f15;
  --ink:#333;
  --muted:#666;
  --line:#d6d9de;
  --band:#eceef1;
  --white:#fff;
}
*{box-sizing:border-box;margin:0;padding:0}
html,body{width:1200px;height:2184px;overflow:hidden}
body{font-family:"Open Sans",sans-serif;color:var(--ink);background:var(--white);position:relative}
.abs{position:absolute}

/* header */
.site-header{left:0;top:0;width:1200px;height:58px;background:var(--white);border-bottom:1px solid var(--line)}
.brand{left:80px;top:12px;font-size:28px;font-weight:700;color:var(--blue)}
.header-call{right:80px;top:10px;display:flex;align-items:center;gap:10px}
.header-call .tag{font-size:10px;color:var(--muted)}
.header-call .num{font-size:16px;font-weight:700;color:var(--blue)}

/* hero */
.hero{left:0;top:58px;width:1200px;height:520px;background:linear-gradient(180deg,#dfe8f2 0%,#c8d4e1 55%,#eef2f6 100%)}
.hero-title{left:0;top:270px;width:1200px;text-align:center;font-size:46px;font-weight:700;color:var(--blue)}
.btn{display:inline-block;background:var(--green);color:var(--white);font-weight:700;border-radius:3px;border-bottom:3px solid var(--green-dark)}
.hero-btn{left:525px;top:345px;width:150px;height:42px;line-height:40px;text-align:center;font-size:15px}
.hero-arrow{top:280px;width:26px;height:40px;background:rgba(255,255,255,.8);display:flex;align-items:center;justify-content:center}

/* lines */
.lines{left:80px;top:515px;width:1040px;display:flex;gap:32px}
.line-card{width:236px;height:290px;background:var(--white);box-shadow:0 4px 14px rgba(0,0,0,.15);text-align:center;position:relative;padding-top:74px}
.line-icon{position:absolute;left:78px;top:-40px;width:80px;height:80px;border-radius:50%;background:var(--navy);border:5px solid var(--white);display:flex;align-items:center;justify-content:center;box-shadow:0 2px 6px rgba(0,0,0,.2)}
.line-card h3{font-size:22px;font-weight:700;color:var(--ink)}
.line-card p{font-size:12px;line-height:17px;color:var(--muted);margin:10px 30px 18px}
.line-card .btn{font-size:11px;padding:5px 14px}

/* agent + form */
.agent-band{left:0;top:860px;width:1200px;height:380px;background:var(--band)}
.agent-card{left:110px;top:880px;width:350px;height:340px;background:var(--white);text-align:center;padding-top:22px}
.agent-photo{width:150px;height:150px;border-radius:50%;margin:0 auto;border:5px solid var(--blue);background:linear-gradient(160deg,#9fb3c9,#54667d)}
.agent-card h2{font-size:21px;font-weight:700;margin-top:16px}
.agent-phone{font-size:15px;font-weight:700;color:var(--ink);margin-top:6px;display:flex;align-items:center;justify-content:center;gap:8px}
.agent-addr{font-size:13px;color:var(--muted);margin-top:10px;line-height:19px}
.quote-form{left:470px;top:880px;width:620px;height:340px;background:var(--white);padding:22px 28px}
.quote-form h2{font-size:21px;font-weight:700;color:var(--ink)}
.quote-form h2 span{color:var(--blue)}
.form-grid{display:grid;grid-template-columns:1fr 1fr;column-gap:30px;row-gap:8px;margin-top:16px;border-top:1px solid var(--line);padding-top:12px}
.field label{display:block;font-size:11px;color:var(--ink);margin-bottom:3px}
.field .input{height:22px;border:1px solid var(--line);border-radius:2px;font-size:10px;color:#999;padding:3px 8px}
.dob{display:flex;gap:6px}
.dob .input{flex:1}
.submit{margin-top:14px;font-size:12px;padding:6px 26px}

/* about */
.about{left:120px;top:1270px;width:960px;text-align:center}
.about h2{font-size:27px;font-weight:700;color:var(--ink)}
.about h2 span{color:var(--blue)}
.about p{font-size:14px;line-height:23px;color:var(--muted);margin-top:16px}

/* reviews */
.review-band{left:0;top:1450px;width:1200px;height:340px;background:var(--band)}
.review-head{left:0;top:1468px;width:1200px;display:flex;justify-content:center;align-items:center;gap:20px}
.review-head h2{font-size:27px;font-weight:700;color:var(--ink)}
.review-head h2 span{color:var(--blue)}
.arrow-box{width:26px;height:26px;background:var(--white);display:flex;align-items:center;justify-content:center;border:1px solid var(--line)}
.review{top:1530px;width:460px;height:230px;background:var(--white);border-radius:10px;padding:22px 28px}
.review .q{font-size:40px;line-height:30px;color:var(--blue);font-weight:700}
.review p{font-size:14px;line-height:22px;color:var(--muted);font-style:normal}
.reviewer{display:flex;align-items:center;gap:14px;margin-top:14px}
.reviewer .avatar{width:54px;height:54px;border-radius:50%;border:3px solid var(--blue);background:linear-gradient(160deg,#b4c2d1,#6b7c90)}
.reviewer .name{font-size:13px;font-weight:700;color:var(--green)}

/* companies */
.company-title{left:0;top:1830px;width:1200px;display:flex;justify-content:center;align-items:center}
.company-title::before,.company-title::after{content:"";width:400px;height:1px;background:var(--line)}
.company-title h2{font-size:27px;font-weight:700;border:1px solid var(--line);padding:4px 22px;color:var(--ink)}
.company-title h2 span{color:var(--blue)}
.partners{left:90px;top:1912px;width:1020px;display:flex;justify-content:space-between;align-items:center}
.partner{display:flex;align-items:center;gap:8px;font-size:22px;font-weight:700;color:#2b2b2b}
.partner .dot{width:14px;height:14px;border-radius:50%;background:#2b2b2b}
.partner .sq{width:14px;height:14px;background:#2b2b2b}

/* footer */
.site-footer{left:0;top:2010px;width:1200px;height:174px;background:var(--blue)}
.disclaimer{left:120px;top:2030px;width:960px;text-align:center;color:var(--white)}
.disclaimer h4{font-size:14px;font-weight:700}
.disclaimer p{font-size:11px;line-height:17px;margin-top:6px;opacity:.9}
.footer-bar{left:0;top:2134px;width:1200px;height:50px;background:var(--blue-dark);display:flex;justify-content:space-between;align-items:center;padding:0 80px;color:var(--white)}
.footer-bar small{font-size:11px}
.footer-bar strong{font-size:24px;font-weight:700}
</style>
</head>
<body>

<header class="abs site-header">
  <div class="abs brand">Insurance Agent</div>
  <div class="abs header-call">
    <svg width="26" height="26" viewBox="0 0 24 24"><path fill="#1f5fae" d="M6.6 10.8a15.1 15.1 0 0 0 6.6 6.6l2.2-2.2a1 1 0 0 1 1-.25 11.4 11.4 0 0 0 3.6.57 1 1 0 0 1 1 1V20a1 1 0 0 1-1 1A17 17 0 0 1 3 4a1 1 0 0 1 1-1h3.5a1 1 0 0 1 1 1c0 1.25.2 2.45.57 3.57a1 1 0 0 1-.25 1z"/></svg>
    <div><div class="tag">Get a quote quickly at</div><div class="num">(555) 014-2270</div></div>
  </div>
</header>

<section class="abs hero" role="img" aria-label="Photo of a field of white umbrellas with one red umbrella standing out"></section>
<div class="abs hero-arrow" style="left:0">
  <svg width="12" height="18" viewBox="0 0 12 18"><path d="M10 2 3 9l7 7" stroke="#555" stroke-width="3" fill="none"/></svg>
</div>
<div class="abs hero-arrow" style="right:0">
  <svg width="12" height="18" viewBox="0 0 12 18"><path d="m2 2 7 7-7 7" stroke="#555" stroke-width="3" fill="none"/></svg>
</div>
<h1 class="abs hero-title">Business Insurance</h1>
<a class="abs btn hero-btn">GET A QUOTE!</a>

<section class="abs lines">
  <div class="line-card">
    <div class="line-icon"><svg width="40" height="40" viewBox="0 0 40 40" fill="#fff"><rect x="6" y="16" width="16" height="12"/><rect x="10" y="8" width="8" height="8" fill="none" stroke="#fff" stroke-width="3"/><rect x="24" y="4" width="3" height="26"/><rect x="27" y="26" width="9" height="3"/><circle cx="10" cy="31" r="4"/><circle cx="20" cy="31" r="4"/></svg></div>
    <h3>Lift</h3>
    <p>Protect the people you love with flexible cover and clear terms.</p>
    <a class="btn">GET A QUOTE!</a>
  </div>
  <div class="line-card">
    <div class="line-icon"><svg width="42" height="40" viewBox="0 0 42 40" fill="#fff"><path d="M8 18 12 8h18l4 10h2a2 2 0 0 1 2 2v10H4V20a2 2 0 0 1 2-2zm6-7-3 7h20l-3-7z"/><rect x="6" y="30" width="7" height="5" rx="1"/><rect x="29" y="30" width="7" height="5" rx="1"/><circle cx="11" cy="24" r="2.5" fill="#123a6e"/><circle cx="31" cy="24" r="2.5" fill="#123a6e"/></svg></div>
    <h3>Auto</h3>
    <p>Drive with confidence knowing your car and passengers are covered.</p>
    <a class="btn">GET A QUOTE!</a>
  </div>
  <div class="line-card">
    <div class="line-icon"><svg width="40" height="40" viewBox="0 0 40 40" fill="#fff"><path d="M20 5 3 20h5v14h9V25h6v9h9V20h5z"/></svg></div>
    <h3>Home</h3>
    <p>Keep your house and belongings safe from fire, theft and storms.</p>
    <a class="btn">GET A QUOTE!</a>
  </div>
  <div class="line-card">
    <div class="line-icon"><svg width="40" height="40" viewBox="0 0 40 40" fill="#fff"><path d="M14 10V7a2 2 0 0 1 2-2h8a2 2 0 0 1 2 2v3h8a2 2 0 0 1 2 2v18a2 2 0 0 1-2 2H6a2 2 0 0 1-2-2V12a2 2 0 0 1 2-2zm3 0h6V8h-6z"/><rect x="4" y="19" width="32" height="2" fill="#123a6e"/></svg></div>
    <h3>Business</h3>
    <p>Guard your company, staff and assets against the unexpected today.</p>
    <a class="btn">GET A QUOTE!</a>
  </div>
</section>

<section class="abs agent-band"></section>
<div class="abs agent-card">
  <div class="agent-photo" role="img" aria-label="Portrait photo of the insurance agent"></div>
  <h2>Owen Parker - Agent</h2>
  <div class="agent-phone">
    <svg width="22" height="22" viewBox="0 0 24 24"><circle cx="12" cy="12" r="12" fill="#1f5fae"/><path fill="#fff" d="M8.6 10.8a9 9 0 0 0 4.6 4.6l1.5-1.5a.7.7 0 0 1 .7-.17 7.5 7.5 0 0 0 2.4.38.7.7 0 0 1 .7.7V17a.7.7 0 0 1-.7.7A11.3 11.3 0 0 1 6.3 6.4a.7.7 0 0 1 .7-.7h2.2a.7.7 0 0 1 .7.7c0 .83.13 1.63.38 2.4a.7.7 0 0 1-.17.7z"/></svg>
    (555) 014-2271
  </div>
  <div class="agent-addr">410 Harbor Ave<br>Lakeview, CA 90012</div>
</div>

<form class="abs quote-form">
  <h2><span>Get An Instant</span> Insurance Quote.</h2>
  <div class="form-grid">
    <div class="field"><label>First Name:</label><div class="input"></div></div>
    <div class="field"><label>Height/Weight:</label><div class="input"></div></div>
    <div class="field"><label>Sex:</label><div class="input">Select</div></div>
    <div class="field"><label>Tobacco Use:</label><div class="input">Select</div></div>
    <div class="field"><label>Date of Birth:</label><div class="dob"><div class="input">Month</div><div class="input">Day</div><div class="input">Year</div></div></div>
    <div class="field"><label>Phone:</label><div class="input"></div></div>
    <div class="field"><label>Current Health:</label><div class="input">Select</div></div>
    <div class="field"><label>Email:</label><div class="input"></div></div>
  </div>
  <a class="btn submit">SUBMIT</a>
</form>

<section class="abs about">
  <h2>About <span>Insurance Agent</span></h2>
  <p>We are an independent agency helping families and business owners find the right insurance at a fair price. Our licensed agents compare plans from trusted carriers, explain every option in plain language and stay with you when it is time to file a claim. Request a free quote today and see how much you could save on your cover.</p>
</section>

<section class="abs review-band"></section>
<div class="abs review-head">
  <div class="arrow-box"><svg width="10" height="14" viewBox="0 0 10 14"><path d="M8 1 2 7l6 6" stroke="#333" stroke-width="2.5" fill="none"/></svg></div>
  <h2><span>Our Customer</span> Review</h2>
  <div class="arrow-box"><svg width="10" height="14" viewBox="0 0 10 14"><path d="m2 1 6 6-6 6" stroke="#333" stroke-width="2.5" fill="none"/></svg></div>
</div>
<blockquote class="abs review" style="left:120px">
  <div class="q">“</div>
  <p>Switching to this agency was easy. They found me better coverage for my home and car and saved me money every month. Friendly, fast and always ready to help.</p>
  <div class="reviewer"><div class="avatar" role="img" aria-label="Customer photo"></div><span class="name">Mr Alan Brooks</span></div>
</blockquote>
<blockquote class="abs review" style="left:620px">
  <div class="q">“</div>
  <p>When my shop had a loss, my agent handled the claim from start to finish. I never felt alone and the payout came quickly. I recommend them to every owner.</p>
  <div class="reviewer"><div class="avatar" role="img" aria-label="Customer photo"></div><span class="name">Mr Chris Hale</span></div>
</blockquote>

<div class="abs company-title"><h2><span>Insurance</span> Company</h2></div>
<div class="abs partners">
  <svg width="14" height="20" viewBox="0 0 14 20"><path d="M12 2 3 10l9 8" stroke="#1f5fae" stroke-width="3" fill="none"/></svg>
  <span class="partner">Dalvorne</span>
  <span class="partner"><span class="dot"></span>Meritwyn</span>
  <span class="partner">Torrasyn</span>
  <span class="partner">Quillmarsh</span>
  <span class="partner"><span class="sq"></span>Halvexa</span>
  <svg width="14" height="20" viewBox="0 0 14 20"><path d="m2 2 9 8-9 8" stroke="#1f5fae" stroke-width="3" fill="none"/></svg>
</div>

<footer class="abs site-footer"></footer>
<div class="abs disclaimer">
  <h4>Disclaimer</h4>
  <p>Insurance products are offered through licensed agents. Rates and availability vary by state and are subject to underwriting approval. Quotes are estimates only and do not bind coverage. Please review your policy documents for full terms, limits and exclusions.</p>
</div>
<div class="abs footer-bar">
  <small>© 2015 Insurance Agent. All Rights Reserved.</small>
  <strong>Insurance Agent</strong>
</div>

</body>
</html>
```